Commercial/Retail/Office Real Estate Lease Brochure for Vacant Space

We need a commercial Real Estate Fyler Template for lease space. We would like it for Vacant lease spaces and new buildings in the commercial, retail, office and industrial lease space. The flyer should have sections for: Highlights (site size, leasable area, Location, Ammenties etc.), concept floor plan or site plan, contact information, project/construction description.

Target Market(s)

Commercial Leasing for Offices and Retail Space

Industry/Entity Type

Real Estate Leasing and Development

Requirements
Must have
• Clean, timeless not overly busy template with spots for key metrics (square feet leaseable space, parking etc), location for pictures
Nice to have
• Marlow Crest Real Estate Logo for header/foot, reusable with adjustments for other spaces
Should not have
• Busy, overall colorfull or contrasting

```html
<!DOCTYPE html>
<html lang="en">
<head>
<meta charset="utf-8">
<title>Marlow Crest Real Estate – Commercial Leasing Flyer</title>
<link href="https://fonts.googleapis.com/css2?family=PT+Sans+Narrow:wght@400;700&family=PT+Sans:wght@400;700&display=swap" rel="stylesheet">
<style>
  :root{
    --orange:#f28a2e;
    --orange-deep:#ef6b2f;
    --pink:#e9476a;
    --navy:#1f3e8c;
    --ink:#4a4a4a;
    --muted:#8c8c8c;
    --paper:#ffffff;
    --plan-paper:#f1f1f1;
    --plan-line:#6a6a6a;
  }
  *{box-sizing:border-box;margin:0;padding:0}
  html,body{width:1200px;height:2568px;overflow:hidden;background:var(--paper)}
  body{position:relative;font-family:"PT Sans",Arial,sans-serif;color:var(--ink)}

  /* preview row */
  .showcase{position:absolute;left:0;top:0;width:1200px;height:870px;
    background:radial-gradient(ellipse 900px 520px at 50% 0%,#f6a15b 0%,#f9c9a0 45%,#fff 100%)}
  .thumb{position:absolute;top:72px;width:1200px;height:1680px;transform:scale(.4333);transform-origin:0 0;
    box-shadow:0 12px 40px rgba(0,0,0,.25)}
  .thumb--site{left:80px}
  .thumb--lease{left:620px}

  .flyer{position:absolute;width:1200px;height:1680px;background:var(--paper);overflow:hidden}
  .flyer--main{left:0;top:888px}

  /* hero */
  .hero-photo{position:absolute;left:0;top:0;width:820px;height:772px;
    background:linear-gradient(180deg,#8fb0cc 0%,#c7d6e0 38%,#b0704f 52%,#9a5b40 70%,#7e8c55 86%,#66753f 100%)}
  .hero-panel{position:absolute;left:820px;top:0;width:380px;height:772px;
    background:linear-gradient(180deg,var(--orange) 0%,var(--orange-deep) 55%,var(--pink) 100%)}
  .hero-panel svg{position:absolute;left:40px;top:192px}
  .hero-title{position:absolute;left:40px;top:322px;font-family:"PT Sans Narrow",Arial,sans-serif;
    color:#fff;font-size:66px;line-height:1.02;font-weight:400}

  /* amenities */
  .section-title{position:absolute;left:68px;font-family:"PT Sans Narrow",Arial,sans-serif;
    color:var(--navy);font-size:56px;font-weight:400;line-height:1}
  .features-title{top:884px}
  .feature-list{position:absolute;top:990px;list-style:none;font-size:19px;line-height:30px;color:var(--muted)}
  .feature-list li::before{content:"";display:inline-block;width:7px;height:7px;border-radius:50%;
    background:var(--muted);margin-right:14px;vertical-align:middle}
  .feature-list--a{left:68px}.feature-list--b{left:412px}.feature-list--c{left:820px}

  /* gallery */
  .gallery-photo{position:absolute;top:1248px;height:304px}
  .gallery-photo--1{left:0;width:388px;background:linear-gradient(180deg,#a9c3d9 0%,#cfdbe3 34%,#9b5e44 58%,#7a5a48 76%,#5f6650 100%)}
  .gallery-photo--2{left:412px;width:376px;background:linear-gradient(180deg,#dfe4e8 0%,#c4cacf 40%,#3c4047 66%,#5a5c60 82%,#8a8a8a 100%)}
  .gallery-photo--3{left:812px;width:388px;background:linear-gradient(180deg,#1b2030 0%,#33343e 42%,#8a6240 64%,#3a2f2a 82%,#1f1f21 100%)}

  /* footer */
  .contact-bar{position:absolute;left:0;top:1560px;width:1200px;height:120px;
    background:linear-gradient(90deg,var(--orange) 0%,var(--orange-deep) 50%,var(--pink) 100%);color:#fff}
  .contact-bar__title{position:absolute;left:64px;top:30px;font-family:"PT Sans Narrow",Arial,sans-serif;font-size:60px;font-weight:400;line-height:1}
  .agent{position:absolute;top:22px;font-size:16px;line-height:20px}
  .agent strong{display:block;font-weight:700}
  .agent--1{left:420px}.agent--2{left:820px}

  /* site plan sheet */
  .page-heading{position:absolute;left:48px;top:20px;font-family:"PT Sans Narrow",Arial,sans-serif;
    color:var(--navy);font-size:68px;font-weight:400;line-height:1}
  .site-plan{position:absolute;left:48px;top:100px;width:1104px;height:840px;
    background:linear-gradient(135deg,#f4f4f4 0%,#dedede 50%,#eeeeee 100%);border:3px solid var(--plan-line)}
  .highlights-title{left:48px;top:990px;font-size:68px}
  .highlight-list{position:absolute;left:48px;top:1100px;list-style:none;font-size:26px;line-height:40px;color:var(--ink)}
  .highlight-list b{color:var(--navy)}
  .location-map{position:absolute;left:690px;top:1000px;width:462px;height:420px;
    background:linear-gradient(135deg,#d8e6cc 0%,#eef0ea 50%,#cfdde8 100%)}
</style>
</head>
<body>

<section class="showcase">
  <div class="thumb thumb--site">
    <article class="flyer">
      <h2 class="page-heading">Site Plan</h2>
      <div class="site-plan" role="img" aria-label="Concept site plan drawing of the building floor layout"></div>
      <h2 class="section-title highlights-title">Property Highlights</h2>
      <ul class="highlight-list">
        <li><b>Site Size:</b> 2.4 Acres</li>
        <li><b>Leasable Area:</b> 18,500 SF</li>
        <li><b>Location:</b> Pembina Corridor</li>
        <li><b>Parking:</b> 64 Stalls</li>
        <li><b>Zoning:</b> C2 Commercial</li>
        <li><b>Available:</b> Spring 2025</li>
        <li><b>Storeys:</b> Two</li>
      </ul>
      <div class="location-map" role="img" aria-label="Location map with property pin"></div>
      <footer class="contact-bar">
        <h3 class="contact-bar__title">Contact Us</h3>
        <p class="agent agent--1"><strong>Dale Morrow</strong>Vice President &amp; Managing Director<br>C + 1 204 555 0142 • T + 1 204 555 0187<br>dale.morrow@marlowcrest.ca</p>
        <p class="agent agent--2"><strong>Evan Whitlock</strong>Vice President<br>C + 1 204 555 0163 • T + 1 204 555 0187<br>evan.whitlock@marlowcrest.ca</p>
      </footer>
    </article>
  </div>

  <div class="thumb thumb--lease">
    <article class="flyer">
      <div class="hero-photo" role="img" aria-label="Rendering of a two-storey brick commercial building"></div>
      <div class="hero-panel">
        <svg width="120" height="120" viewBox="0 0 120 120" aria-hidden="true"><rect x="4" y="4" width="112" height="112" rx="8" fill="none" stroke="#fff" stroke-width="6"/><path d="M34 86 L86 34 M60 34 H86 V60 M34 60 V86 H60" fill="none" stroke="#fff" stroke-width="7"/></svg>
        <h1 class="hero-title">Commercial<br>Leasing<br>Opportunity</h1>
      </div>
      <h2 class="section-title features-title">Amenities &nbsp;+ Features</h2>
      <ul class="feature-list feature-list--a"><li>18,500 SF leasable area</li><li>Units from 1,200 SF</li><li>Two-storey building</li><li>Ground-floor retail frontage</li><li>Second-floor office suites</li><li>Elevator access</li><li>Barrier-free entrances</li><li>Flexible demising options</li></ul>
      <ul class="feature-list feature-list--b"><li>64 surface parking stalls</li><li>Pylon signage available</li><li>High-traffic corridor</li><li>Transit stop on site</li><li>Full-height glazing</li><li>New high-efficiency HVAC</li><li>Fibre internet ready</li><li>C2 commercial zoning</li></ul>
      <ul class="feature-list feature-list--c"><li>Occupancy Spring 2025</li><li>Tenant improvement allowance</li><li>Secure bicycle storage</li><li>EV charging stations</li><li>Landscaped grounds</li><li>On-site management</li><li>Close to major highways</li><li>Shared loading area</li></ul>
      <div class="gallery-photo gallery-photo--1" role="img" aria-label="Building corner view by day"></div>
      <div class="gallery-photo gallery-photo--2" role="img" aria-label="Building entrance with signage"></div>
      <div class="gallery-photo gallery-photo--3" role="img" aria-label="Building lit at dusk"></div>
      <footer class="contact-bar">
        <h3 class="contact-bar__title">Contact Us</h3>
        <p class="agent agent--1"><strong>Dale Morrow</strong>Vice President &amp; Managing Director<br>C + 1 204 555 0142 • T + 1 204 555 0187<br>dale.morrow@marlowcrest.ca</p>
        <p class="agent agent--2"><strong>Evan Whitlock</strong>Vice President<br>C + 1 204 555 0163 • T + 1 204 555 0187<br>evan.whitlock@marlowcrest.ca</p>
      </footer>
    </article>
  </div>
</section>

<article class="flyer flyer--main">
  <div class="hero-photo" role="img" aria-label="Rendering of a two-storey brick commercial building"></div>
  <div class="hero-panel">
    <svg width="120" height="120" viewBox="0 0 120 120" aria-hidden="true"><rect x="4" y="4" width="112" height="112" rx="8" fill="none" stroke="#fff" stroke-width="6"/><path d="M34 86 L86 34 M60 34 H86 V60 M34 60 V86 H60" fill="none" stroke="#fff" stroke-width="7"/></svg>
    <h1 class="hero-title">Commercial<br>Leasing<br>Opportunity</h1>
  </div>
  <h2 class="section-title features-title">Amenities &nbsp;+ Features</h2>
  <ul class="feature-list feature-list--a"><li>18,500 SF leasable area</li><li>Units from 1,200 SF</li><li>Two-storey building</li><li>Ground-floor retail frontage</li><li>Second-floor office suites</li><li>Elevator access</li><li>Barrier-free entrances</li><li>Flexible demising options</li></ul>
  <ul class="feature-list feature-list--b"><li>64 surface parking stalls</li><li>Pylon signage available</li><li>High-traffic corridor</li><li>Transit stop on site</li><li>Full-height glazing</li><li>New high-efficiency HVAC</li><li>Fibre internet ready</li><li>C2 commercial zoning</li></ul>
  <ul class="feature-list feature-list--c"><li>Occupancy Spring 2025</li><li>Tenant improvement allowance</li><li>Secure bicycle storage</li><li>EV charging stations</li><li>Landscaped grounds</li><li>On-site management</li><li>Close to major highways</li><li>Shared loading area</li></ul>
  <div class="gallery-photo gallery-photo--1" role="img" aria-label="Building corner view by day"></div>
  <div class="gallery-photo gallery-photo--2" role="img" aria-label="Building entrance with signage"></div>
  <div class="gallery-photo gallery-photo--3" role="img" aria-label="Building lit at dusk"></div>
  <footer class="contact-bar">
    <h3 class="contact-bar__title">Contact Us</h3>
    <p class="agent agent--1"><strong>Dale Morrow</strong>Vice President &amp; Managing Director<br>C + 1 204 555 0142 • T + 1 204 555 0187<br>dale.morrow@marlowcrest.ca</p>
    <p class="agent agent--2"><strong>Evan Whitlock</strong>Vice President<br>C + 1 204 555 0163 • T + 1 204 555 0187<br>evan.whitlock@marlowcrest.ca</p>
  </footer>
</article>

</body>
</html>
```